Card Design for my dog training business Brightpaw Obedience

Need a business card design for my dog training business with my new logo. Want the card to come off professional yet fun. Want it to be very eye catchy as well. I normally have these at vet clinics, pet stores, and groomers. so need it to look better than my competitors.
Target Market(s)
dog owners
Industry/Entity Type
Dog Training
Contact Information for Business Card
needs logo, my name and info
Font styles to use
Serif
Colors
0255a3
ffffff
ec1f27
000000
333333
fbfbfb
Requirements
Must have
- Brightpaw Obedience
- Felix Orland
- 415 903 2276
- info@brightpawobedience.example
- www.brightpawobedience.example

```html
<!DOCTYPE html>
<html lang="en">
<head>
<meta charset="utf-8">
<title>Brightpaw Obedience – Business Card</title>
<link href="https://fonts.googleapis.com/css2?family=Roboto:wght@400;700&family=EB+Garamond:ital@1&display=swap" rel="stylesheet">
<style>
  :root {
    --page-bg: #e4e4e4;
    --card-light: #ffffff;
    --card-dark: #231f20;
    --ink: #222222;
    --ink-soft: #444444;
    --rule: #bdbdbd;
    --on-dark: #ffffff;
  }
  html, body {
    margin: 0;
    padding: 0;
    width: 1125px;
    height: 1200px;
    overflow: hidden;
    background: var(--page-bg);
  }
  .canvas {
    position: relative;
    width: 1125px;
    height: 1200px;
  }
  .card {
    position: absolute;
    left: 171px;
    width: 826px;
    height: 471px;
    box-sizing: border-box;
  }
  .card--front {
    top: 106px;
    background: var(--card-light);
  }
  .card--back {
    top: 640px;
    background: var(--card-dark);
  }

  /* Front */
  .brand-mark {
    position: absolute;
    left: 70px;
    top: 150px;
    width: 300px;
    height: 170px;
    display: flex;
    flex-direction: column;
    align-items: center;
    justify-content: center;
    gap: 12px;
  }
  .brand-mark__dot {
    width: 22px;
    height: 22px;
    border-radius: 50%;
    background: var(--ink);
  }
  .brand-mark__name {
    font-family: "Roboto", sans-serif;
    font-weight: 700;
    font-size: 28px;
    line-height: 1.15;
    color: var(--ink);
    text-align: center;
  }
  .divider {
    position: absolute;
    left: 382px;
    top: 157px;
    width: 1px;
    height: 163px;
    background: var(--rule);
  }
  .contact {
    position: absolute;
    left: 428px;
    top: 168px;
    font-family: "Roboto", sans-serif;
  }
  .contact__name {
    margin: 0 0 18px;
    font-size: 31px;
    font-weight: 700;
    color: var(--ink);
    letter-spacing: 0.2px;
  }
  .contact__list {
    list-style: none;
    margin: 0;
    padding: 0;
  }
  .contact__item {
    display: flex;
    align-items: center;
    gap: 12px;
    font-size: 20px;
    line-height: 26px;
    color: var(--ink-soft);
  }
  .contact__icon {
    width: 17px;
    height: 17px;
    flex: none;
    fill: var(--ink);
  }

  /* Back */
  .back-mark {
    position: absolute;
    left: 0;
    right: 0;
    top: 110px;
    height: 210px;
    display: flex;
    flex-direction: column;
    align-items: center;
    justify-content: center;
    gap: 18px;
  }
  .back-mark__dot {
    width: 36px;
    height: 36px;
    border-radius: 50%;
    background: var(--on-dark);
  }
  .back-mark__name {
    font-family: "Roboto", sans-serif;
    font-weight: 700;
    font-size: 52px;
    color: var(--on-dark);
    text-align: center;
  }
  .tagline {
    position: absolute;
    left: 0;
    right: 0;
    top: 392px;
    margin: 0;
    text-align: center;
    font-family: "EB Garamond", serif;
    font-style: italic;
    font-size: 24px;
    color: var(--on-dark);
  }
</style>
</head>
<body>
<main class="canvas">

  <section class="card card--front" aria-label="Business card front">
    <div class="brand-mark">
      <span class="brand-mark__dot"></span>
      <span class="brand-mark__name">Brightpaw<br>Obedience</span>
    </div>

    <div class="divider"></div>

    <div class="contact">
      <h1 class="contact__name">Felix Orland</h1>
      <ul class="contact__list">
        <li class="contact__item">
          <svg class="contact__icon" viewBox="0 0 24 24" aria-hidden="true">
            <path d="M6.6 10.8c1.4 2.8 3.8 5.1 6.6 6.6l2.2-2.2c.3-.3.7-.4 1-.2 1.1.4 2.3.6 3.6.6.6 0 1 .4 1 1V20c0 .6-.4 1-1 1C10.6 21 3 13.4 3 4c0-.6.4-1 1-1h3.5c.6 0 1 .4 1 1 0 1.3.2 2.5.6 3.6.1.3 0 .7-.2 1l-2.3 2.2z"/>
          </svg>
          415 903 2276
        </li>
        <li class="contact__item">
          <svg class="contact__icon" viewBox="0 0 24 24" aria-hidden="true">
            <path d="M3 6h18v12H3z M4.5 7.5v.4l7.5 5 7.5-5v-.4z" fill-rule="evenodd"/>
          </svg>
          info@brightpawobedience.example
        </li>
        <li class="contact__item">
          <svg class="contact__icon" viewBox="0 0 24 24" aria-hidden="true">
            <path d="M12 2a10 10 0 1 0 0 20 10 10 0 0 0 0-20zm-1 17.9A8 8 0 0 1 4.2 10L9 14.8V16c0 1.1.9 2 2 2v1.9zm6.9-2.5c-.3-.8-1-1.4-1.9-1.4h-1v-3c0-.6-.4-1-1-1H8v-2h2c.6 0 1-.4 1-1V7h2c1.1 0 2-.9 2-2v-.4a8 8 0 0 1 2.9 12.8z"/>
          </svg>
          www.brightpawobedience.example
        </li>
      </ul>
    </div>
  </section>

  <section class="card card--back" aria-label="Business card back">
    <div class="back-mark">
      <span class="back-mark__dot"></span>
      <span class="back-mark__name">Brightpaw Obedience</span>
    </div>
    <p class="tagline">“Training dogs across Texas one dog at a time.”</p>
  </section>

</main>
</body>
</html>
```